Seeking funky, innovative business cards

I am looking to refresh our current business cards to something more engaging, visual and impactful. We are a management consultancy firm, see website (www.larkstone-partners.com.au). I've included our colour scheme, sample of the slides we use and our old business cards. We would like our cards to have icons. The card should display:- Name- Title- Mobile number- Address- Email address- Website - Company logo- Our purpose statement "we shape workplaces where people love to be"

Contact Information for Business Card

Brennan Ulfsson
Consultant
0468 927 341
Level 3, 218 Wexley Street, Melbourne 3000
brennan@larkstone-partners.com.au
www.larkstone-partners.com.au

Purpose statement "we shape workplaces where people love to be"
LOGO available in google images

Font styles to use
Other font styles liked:
• Open Sans Light, Bebas Neue (open to other cool foints)

Colors
ffc214
5c5c5c
f5f5f5
fefefe

Requirements
Must have
• - Name
• - Title
• - Mobile number
• - Address
• - Email address
• - Website
• - Company logo
• - Our purpose statement "we shape workplaces where people love to be"
Nice to have
• - Icons
• - Colour (see our colour scheme"

```html
<!DOCTYPE html>
<html lang="en">
<head>
<meta charset="utf-8">
<title>Larkstone Partners — Business Cards</title>
<link href="https://fonts.googleapis.com/css2?family=Open+Sans:wght@300;400;600&display=swap" rel="stylesheet">
<style>
  :root {
    --backdrop: #1b1b1d;
    --card: #232427;
    --gold: #ffc214;
    --white: #fefefe;
    --soft: #f5f5f5;
    --grey: #5c5c5c;
  }
  * { margin: 0; padding: 0; box-sizing: border-box; }
  html, body { width: 1200px; height: 800px; overflow: hidden; background: var(--backdrop); }
  body { position: relative; font-family: "Open Sans", Arial, sans-serif; color: var(--white); }

  .card {
    position: absolute;
    width: 560px;
    height: 320px;
    background: var(--card);
    border-radius: 4px;
    box-shadow: 0 18px 40px rgba(0,0,0,.55);
    overflow: hidden;
  }
  .card--front { left: 60px; top: 70px; }
  .card--back  { left: 580px; top: 410px; }

  .wordmark { display: flex; align-items: center; gap: 12px; }
  .wordmark__dot { width: 12px; height: 12px; border-radius: 50%; background: var(--gold); flex: none; }
  .wordmark__name { font-weight: 300; color: var(--white); letter-spacing: .5px; white-space: nowrap; }

  .card--front .wordmark { position: absolute; left: 100px; top: 112px; }
  .card--front .wordmark__name { font-size: 44px; }
  .purpose {
    position: absolute; left: 124px; top: 182px;
    font-size: 15px; font-weight: 600; font-style: italic; color: var(--soft);
    letter-spacing: .3px; white-space: nowrap;
  }

  .card--back .wordmark { position: absolute; left: 36px; top: 40px; }
  .card--back .wordmark__name { font-size: 36px; }

  .person { position: absolute; left: 36px; top: 150px; }
  .person__name { font-size: 21px; font-weight: 600; color: var(--white); white-space: nowrap; }
  .person__title { font-size: 15px; color: var(--gold); margin-top: 1px; }

  .divider {
    position: absolute; left: 235px; top: 166px; width: 295px; height: 1px;
    background: var(--gold);
  }

  .contacts { position: absolute; left: 36px; top: 212px; list-style: none; }
  .contacts li { display: flex; align-items: center; gap: 9px; font-size: 13px; color: var(--soft); line-height: 22px; white-space: nowrap; }
  .contacts .accent { color: var(--gold); }
  .icon { width: 15px; height: 15px; flex: none; }

  .address {
    position: absolute; right: 30px; top: 200px; text-align: left;
    font-size: 13px; color: var(--soft); line-height: 19px; white-space: nowrap;
  }

  .band { position: absolute; left: 0; bottom: 0; width: 100%; height: 8px; background: var(--gold); }
</style>
</head>
<body>

  <section class="card card--front" aria-label="Card front">
    <div class="wordmark">
      <span class="wordmark__dot"></span>
      <span class="wordmark__name">Larkstone Partners</span>
    </div>
    <p class="purpose">we shape workplaces where people love to be</p>
  </section>

  <section class="card card--back" aria-label="Card back">
    <div class="wordmark">
      <span class="wordmark__dot"></span>
      <span class="wordmark__name">Larkstone Partners</span>
    </div>

    <div class="person">
      <p class="person__name">Brennan Ulfsson</p>
      <p class="person__title">Consultant</p>
    </div>
    <span class="divider"></span>

    <ul class="contacts">
      <li>
        <svg class="icon" viewBox="0 0 16 16"><circle cx="8" cy="8" r="8" fill="#ffc214"/><path d="M5.3 4.2l1.4 1.6-.7 1c.5 1.1 1.3 1.9 2.4 2.4l1-.7 1.6 1.4-.8 1.2C7.6 10.9 5.1 8.4 4.1 5z" fill="#232427"/></svg>
        0468 927 341
      </li>
      <li>
        <svg class="icon" viewBox="0 0 16 16"><circle cx="8" cy="8" r="8" fill="#ffc214"/><rect x="4" y="5.2" width="8" height="5.6" fill="#232427"/><path d="M4 5.4l4 3 4-3" stroke="#ffc214" stroke-width=".9" fill="none"/></svg>
        brennan@larkstone-partners.com.au
      </li>
      <li>
        <svg class="icon" viewBox="0 0 16 16"><circle cx="8" cy="8" r="8" fill="#ffc214"/><g stroke="#232427" stroke-width=".9" fill="none"><circle cx="8" cy="8" r="4.2"/><ellipse cx="8" cy="8" rx="1.8" ry="4.2"/><path d="M3.8 8h8.4"/></g></svg>
        <span>www.<span class="accent">larkstone-partners</span>.com.au</span>
      </li>
    </ul>

    <p class="address">Level 3, 218 Wexley Street<br>Melbourne 3000</p>

    <span class="band"></span>
  </section>

</body>
</html>
```